Vantoq Business Card Project showing the logo and a marbo image on the rear

Design a whacky but professional business card, the logo is for the front and the Marbo image is for the rear. Happy to consider other open source Marbo Images if the designer wants to select one from the web. Vantoq is a competitor to OMB.com.au and Pellory.com.au and is based around every property in Australia

Target Market(s)

Business

Contact Information for Business Card

Name, Title, Email, Web, Phone Number

Font styles to use
Other font styles liked:
• avenir

Requirements
Must have
• Image on Back logo on front
Nice to have
• Happy to consider other images on rear, preftably Colin Marbo. Image supplied I own, we can use open source other Marbo Images

```html
<!DOCTYPE html>
<html lang="en">
<head>
<meta charset="utf-8">
<title>Vantoq Business Card</title>
<link rel="stylesheet" href="https://fonts.googleapis.com/css2?family=Nunito+Sans:wght@400;600;700;800&display=swap">
<style>
  :root {
    --stage: #2b2b2d;
    --card-white: #ffffff;
    --ink: #111111;
    --ink-soft: #4a4a4a;
    --brand-orange: #f28c1c;
    --sky-blue: #3f9ee0;
    --night-blue: #2d5fb8;
    --city-red: #e0453a;
    --city-yellow: #f3c21c;
    --city-green: #2f8a3a;
    --city-teal: #1fa3b8;
  }
  * { box-sizing: border-box; margin: 0; padding: 0; }
  html, body {
    width: 1200px; height: 900px; overflow: hidden;
    background: var(--stage);
    font-family: "Nunito Sans", "Avenir", sans-serif;
  }
  .canvas { position: relative; width: 1200px; height: 900px; }

  .card {
    position: absolute; left: 250px; width: 700px; height: 400px;
    border-radius: 26px; overflow: hidden;
    box-shadow: 0 14px 30px rgba(0,0,0,.45);
  }

  /* Rear of card */
  .card-rear { top: 30px; }
  .rear-artwork {
    position: absolute; inset: 0;
    background:
      linear-gradient(180deg, var(--sky-blue) 0%, var(--night-blue) 32%, transparent 48%),
      linear-gradient(90deg, var(--city-red) 0%, var(--city-yellow) 22%, var(--city-green) 42%, var(--brand-orange) 62%, var(--city-red) 80%, var(--city-teal) 100%);
  }
  .rear-shade {
    position: absolute; left: 0; right: 0; top: 110px; height: 150px;
    background: rgba(0,0,0,.28);
  }
  .rear-logo {
    position: absolute; left: 0; right: 0; top: 140px;
    display: flex; align-items: center; justify-content: center; gap: 18px;
  }
  .rear-logo .logo-square { width: 64px; height: 64px; background: #ffffff; }
  .rear-logo .logo-name {
    color: #ffffff; font-weight: 800; font-size: 84px; line-height: 1;
    letter-spacing: 1px;
  }

  /* Front of card */
  .card-front { top: 470px; background: var(--card-white); }
  .front-logo {
    position: absolute; left: 0; right: 0; top: 52px;
    display: flex; align-items: center; justify-content: center; gap: 20px;
  }
  .front-logo .logo-square { width: 70px; height: 70px; background: var(--brand-orange); }
  .front-logo .logo-name {
    color: var(--ink); font-weight: 800; font-size: 96px; line-height: 1;
    letter-spacing: 1px;
  }

  .person {
    position: absolute; left: 70px; top: 200px; width: 270px; text-align: right;
  }
  .person-name {
    color: var(--brand-orange); font-weight: 800; font-size: 27px;
    letter-spacing: .5px; text-transform: uppercase;
  }
  .person-title { color: var(--ink-soft); font-size: 20px; margin-top: 2px; }

  .divider {
    position: absolute; left: 362px; top: 198px; width: 1.5px; height: 84px;
    background: var(--ink);
  }

  .contacts {
    position: absolute; left: 384px; top: 196px; list-style: none;
  }
  .contacts li {
    display: flex; align-items: center; gap: 10px;
    color: var(--ink-soft); font-size: 20px; line-height: 29px;
  }
  .contact-icon { width: 20px; height: 20px; flex: none; }

  .address-band {
    position: absolute; left: 0; right: 0; bottom: 0; height: 86px;
    border-top: 24px solid var(--ink); border-bottom: 12px solid var(--ink);
    background: var(--card-white);
    display: flex; align-items: center; justify-content: center;
  }
  .address {
    color: var(--ink); font-size: 21px; font-weight: 600; letter-spacing: .3px;
  }
</style>
</head>
<body>
<main class="canvas">

  <section class="card card-rear">
    <div class="rear-artwork" role="img" aria-label="Colourful naive-style city illustration of bright buildings under a blue sky"></div>
    <div class="rear-shade"></div>
    <div class="rear-logo">
      <span class="logo-square"></span>
      <span class="logo-name">Vantoq</span>
    </div>
  </section>

  <section class="card card-front">
    <div class="front-logo">
      <span class="logo-square"></span>
      <span class="logo-name">Vantoq</span>
    </div>

    <div class="person">
      <p class="person-name">Owen Calloway</p>
      <p class="person-title">Executive Producer</p>
    </div>

    <div class="divider"></div>

    <ul class="contacts">
      <li>
        <svg class="contact-icon" viewBox="0 0 20 20" aria-hidden="true">
          <circle cx="10" cy="10" r="10" fill="var(--brand-orange)"/>
          <path d="M7 5.5c.6-.4 1.2-.2 1.5.4l.7 1.5c.2.5 0 1-.4 1.3l-.5.3c.5 1.3 1.4 2.2 2.7 2.7l.3-.5c.3-.4.8-.6 1.3-.4l1.5.7c.6.3.8.9.4 1.5-.6 1-1.7 1.4-2.8 1C9 13.1 6.9 11 6 8.3c-.4-1.1 0-2.2 1-2.8z" fill="#fff"/>
        </svg>
        <span>323-555-0147</span>
      </li>
      <li>
        <svg class="contact-icon" viewBox="0 0 20 20" aria-hidden="true">
          <circle cx="10" cy="10" r="10" fill="var(--brand-orange)"/>
          <rect x="5" y="6.5" width="10" height="7" fill="#fff"/>
          <path d="M5 6.5l5 4 5-4" fill="none" stroke="var(--brand-orange)" stroke-width="1.2"/>
        </svg>
        <span>Owen@vantoq.com.au</span>
      </li>
      <li>
        <svg class="contact-icon" viewBox="0 0 20 20" aria-hidden="true">
          <circle cx="10" cy="10" r="10" fill="var(--brand-orange)"/>
          <circle cx="10" cy="10" r="5" fill="none" stroke="#fff" stroke-width="1.3"/>
          <ellipse cx="10" cy="10" rx="2.2" ry="5" fill="none" stroke="#fff" stroke-width="1.1"/>
          <line x1="5" y1="10" x2="15" y2="10" stroke="#fff" stroke-width="1.1"/>
        </svg>
        <span>www.vantoq.com.au</span>
      </li>
    </ul>

    <div class="address-band">
      <p class="address">1400 W Harlow Street Denby County name 5231</p>
    </div>
  </section>

</main>
</body>
</html>
```